Business Card Design

Online clothing womens clothing store, I sell my clothing online and at the markets.

i would like the attached picture on the front of the card and the contact information on the back.

Industry/Entity Type

Business

Contact Information for Business Card

Marlow Thread
Karen Whitfield
(Instagram symbol) _marlow_thread_
(Facebook symbol) www.fakebookexample.com/marlowthreadau/

W : www.marlowthread.example.au
E : info@marlowthread.example.au
P : 0498716204

```html
<!DOCTYPE html>
<html lang="en">
<head>
<meta charset="utf-8">
<title>Marlow Thread – Business Card</title>
<link href="https://fonts.googleapis.com/css2?family=Barlow:wght@300&family=Barlow+Condensed:wght@500&family=Open+Sans:wght@400;700&display=swap" rel="stylesheet">
<style>
  :root {
    --backdrop: #d6d6d6;
    --card-dark: #050505;
    --ink-light: #f2f2f2;
    --ink-soft: #e6e6e6;
    --photo-light: #d3d9db;
    --photo-mid: #9ea8ae;
    --photo-dark: #3f434d;
  }
  * { margin: 0; padding: 0; box-sizing: border-box; }
  html, body { width: 1189px; height: 1200px; overflow: hidden; }
  body { background: var(--backdrop); position: relative; font-family: "Open Sans", sans-serif; }

  .card { position: absolute; left: 140px; width: 918px; height: 522px; overflow: hidden; }
  .card--contact { top: 47px; background: var(--card-dark); color: var(--ink-light); }
  .card--cover { top: 624px; }

  .brand-mark { position: absolute; left: 0; top: 96px; width: 918px; height: 64px; }
  .brand-mark text { font-family: "Barlow", sans-serif; font-weight: 300; fill: var(--ink-soft); }

  .holder-name { position: absolute; left: 109px; top: 270px; font-size: 33px; font-weight: 700; line-height: 44px; }
  .divider { position: absolute; left: 408px; top: 233px; width: 3px; height: 126px; background: var(--ink-light); }

  .contact-line { position: absolute; display: flex; align-items: center; font-size: 23px; line-height: 28px; white-space: nowrap; }
  .contact-line svg { width: 20px; height: 20px; margin-right: 10px; flex: none; }
  .contact-line .social-dot { width: 20px; height: 20px; background: var(--ink-light); margin-right: 8px; flex: none; }

  .cover-photo { position: absolute; inset: 0;
    background: linear-gradient(100deg, var(--photo-light) 0%, var(--photo-light) 38%, var(--photo-mid) 58%, var(--photo-dark) 80%, var(--photo-dark) 100%); }
  .cover-name { position: absolute; left: 0; top: 344px; width: 918px; height: 130px; }
  .cover-name text { font-family: "Barlow Condensed", sans-serif; font-weight: 500; fill: var(--ink-soft); }
</style>
</head>
<body>

<section class="card card--contact">
  <svg class="brand-mark" viewBox="0 0 918 64">
    <text x="459" y="52" text-anchor="middle" font-size="56" textLength="610" lengthAdjust="spacing">MARLOW THREAD</text>
  </svg>

  <div class="holder-name">Karen Whitfield</div>
  <div class="divider"></div>

  <div class="contact-line" style="left:446px; top:265px;">
    <svg viewBox="0 0 20 20"><rect width="20" height="20" fill="#f2f2f2"/><path d="M6 4c1 0 2 3 2 4s-1 1-1 2 2 3 3 3 1-1 2-1 4 1 4 2-1 2-3 2C9 16 4 11 4 7c0-2 1-3 2-3z" fill="#050505"/></svg>
    <span>0498716204</span>
  </div>
  <div class="contact-line" style="left:446px; top:293px;">
    <svg viewBox="0 0 20 20"><rect y="3" width="20" height="14" fill="#f2f2f2"/><path d="M2 5l8 6 8-6" stroke="#050505" stroke-width="1.6" fill="none"/></svg>
    <span>info@marlowthread.example.au</span>
  </div>
  <div class="contact-line" style="left:446px; top:320px;">
    <svg viewBox="0 0 20 20"><rect width="20" height="20" fill="#f2f2f2"/><circle cx="10" cy="10" r="6" stroke="#050505" stroke-width="1.6" fill="none"/><path d="M4 10h12M10 4c-3 3-3 9 0 12M10 4c3 3 3 9 0 12" stroke="#050505" stroke-width="1.2" fill="none"/></svg>
    <span>www.marlowthread.example.au</span>
  </div>

  <div class="contact-line" style="left:258px; top:365px;">
    <span class="social-dot"></span><span>marlow_thread</span>
  </div>
  <div class="contact-line" style="left:258px; top:394px;">
    <span class="social-dot"></span><span>www.fakebookexample.com/marlowthreadau/</span>
  </div>
</section>

<section class="card card--cover">
  <div class="cover-photo" role="img" aria-label="Misty grey-blue fashion photograph of a person with long hair seen in profile"></div>
  <svg class="cover-name" viewBox="0 0 918 130">
    <text x="31" y="118" font-size="140" textLength="861" lengthAdjust="spacingAndGlyphs">MARLOW THREAD</text>
  </svg>
</section>

</body>
</html>
```